Business card design

Hi,
I need to have a business card design based on the current logo.
If competitive I not put it out to everyone.

It can be single of double sided

Target Market(s)

Food businesses

Industry/Entity Type

Food Manufacturing

Contact Information for Business Card

Details will on card will be as follows Name = Marcus Bell Email = Marcus@PanHearth.com.au Phone = 0418563207 Address = 57 Larkin Street , Kelmarsh Vale NSW 2790 Australia

Font styles to use
Other font styles liked:
• based on two fonts - Adelle & Museo

Requirements
Must have
• Based on the on switch concept

```html
<!DOCTYPE html>
<html lang="en">
<head>
<meta charset="utf-8">
<title>PanHearth Business Card</title>
<link href="https://fonts.googleapis.com/css2?family=Karla:wght@400;500;700&family=Zilla+Slab:wght@600&display=swap" rel="stylesheet">
<style>
  :root {
    --backdrop: #d8d3cb;
    --card: #efeeec;
    --card-edge: #c9c6c2;
    --ink: #231f20;
    --text: #3a3536;
    --red: #d12a3a;
    --red-deep: #b5121f;
    --white: #ffffff;
  }
  html, body {
    margin: 0;
    padding: 0;
    width: 1200px;
    height: 969px;
    overflow: hidden;
    background: var(--backdrop);
  }
  .card {
    position: absolute;
    left: 184px;
    top: 225px;
    width: 868px;
    height: 494px;
    background: var(--card);
    border: 1px solid var(--card-edge);
    border-radius: 28px;
    overflow: hidden;
    font-family: "Karla", sans-serif;
    color: var(--text);
  }
  .edge-tab {
    position: absolute;
    left: 0;
    top: 264px;
    width: 14px;
    height: 146px;
    background: var(--ink);
    border-radius: 0 6px 6px 0;
  }
  .brand {
    position: absolute;
    left: 74px;
    top: 88px;
    width: 350px;
  }
  .brand-name {
    display: flex;
    align-items: center;
    gap: 12px;
    font-weight: 700;
    font-size: 50px;
    line-height: 56px;
    letter-spacing: 1px;
    color: var(--ink);
  }
  .brand-dot {
    width: 38px;
    height: 38px;
    border-radius: 50%;
    background: var(--red);
    flex: none;
  }
  .tagline {
    margin-top: 2px;
    text-align: right;
    font-family: "Zilla Slab", serif;
    font-weight: 600;
    font-size: 16px;
    color: var(--ink);
  }
  .contact {
    position: absolute;
    left: 72px;
    top: 264px;
    list-style: none;
    margin: 0;
    padding: 0;
    font-size: 19px;
    letter-spacing: 0.6px;
  }
  .contact li {
    display: flex;
    align-items: flex-start;
    gap: 8px;
    line-height: 24.5px;
  }
  .contact .address { margin-bottom: 6px; }
  .contact svg {
    flex: none;
    width: 16px;
    height: 16px;
    margin-top: 4px;
    fill: var(--red);
  }
  .name-band {
    position: absolute;
    left: 548px;
    top: 307px;
    width: 320px;
    height: 60px;
    background: linear-gradient(90deg, var(--red) 0%, var(--red-deep) 100%);
    border-radius: 30px 0 0 30px;
    display: flex;
    align-items: center;
    padding-left: 74px;
    box-sizing: border-box;
    color: var(--white);
    font-weight: 500;
    font-size: 29px;
    letter-spacing: 2px;
    text-transform: uppercase;
    white-space: nowrap;
  }
</style>
</head>
<body>
  <div class="card">
    <div class="edge-tab"></div>

    <div class="brand">
      <div class="brand-name"><span class="brand-dot"></span>PANHEARTH</div>
      <div class="tagline">Fresh Kitchen Made Daily</div>
    </div>

    <ul class="contact">
      <li class="address">
        <svg viewBox="0 0 16 16" aria-hidden="true"><path d="M8 0a5.5 5.5 0 0 0-5.5 5.5C2.5 10 8 16 8 16s5.5-6 5.5-10.5A5.5 5.5 0 0 0 8 0zm0 8a2.5 2.5 0 1 1 0-5 2.5 2.5 0 0 1 0 5z"/></svg>
        <span>57 Larkin Street<br>Kelmarsh Vale<br>NSW 2790 Australia</span>
      </li>
      <li>
        <svg viewBox="0 0 16 16" aria-hidden="true"><path d="M3.6 1l2.3 3.2-1.4 1.7c.9 2 2.6 3.7 4.6 4.6l1.7-1.4L14 11.4 12.6 14C6.6 14 2 9.4 2 3.4L3.6 1z"/></svg>
        <span>0418563207</span>
      </li>
      <li>
        <svg viewBox="0 0 16 16" aria-hidden="true"><path d="M1 3.5h14v9H1z M1 3.5l7 5 7-5" stroke="#efeeec" stroke-width="1"/></svg>
        <span>Marcus@PanHearth.com.au</span>
      </li>
      <li>
        <svg viewBox="0 0 16 16" aria-hidden="true"><circle cx="8" cy="8" r="7.5"/><path d="M4 5c2 0 2 2 3 3s-1 3 0 5M10 2c-1 2 1 3 2 3s1 2 3 2" stroke="#efeeec" stroke-width="1.2" fill="none"/></svg>
        <span>www.PanHearth.com.au</span>
      </li>
    </ul>

    <div class="name-band">Marcus Bell</div>
  </div>
</body>
</html>
```